Detail Shop Business card design

i need a business card design for my new detailing company called 'Brisk's Polish Works'. i want an all black and white design . simple, direct and to the point. i want the designer to choose a fitting font to match the logothe front should have logo, address, phone and email and the back side should have a slogan and text indicating that we offer services on anything including cars, trucks, motorcycles and RVs. slogan will read "we take pride in your ride"
maybe also very small on the back side the IG icon with Brisks_Polish_Works

phone 208.417.6352
address 3847 E Larkin Ave
Spokane WA 99214
email: BrisksPolish@mailvexo.com

Target Market(s)

all ages , auto enthusiasts

Industry/Entity Type

Automotive

Contact Information for Business Card

the front should have logo, address, phone and email and the back side should have a slogan and text indicating that we offer services on anything including cars, trucks, motorcycles and RVs. slogan will read "we take pride in your ride"

phone 208.417.6352
address 3847 E Larkin Ave
Spokane WA 99214

Colors
000000
ffffff

Requirements
Must have
• bold font and very simple design with good spacing
Nice to have
• anything creative from the designer indicating we service any types of vehicles
Should not have
• any colors ,

```html
<!DOCTYPE html>
<html lang="en">
<head>
<meta charset="utf-8">
<title>Brisk's Polish Works – Business Card</title>
<link rel="stylesheet" href="https://fonts.googleapis.com/css2?family=Arvo:wght@400;700&family=PT+Serif&family=Fjalla+One&family=Roboto:wght@700&display=swap">
<style>
  :root {
    --ink: #000000;
    --paper: #ffffff;
    --back-paper: #f2f2f2;
    --backdrop: #e8e6e3;
    --art-light: #e4e4e4;
    --art-mid: #6a6a6a;
    --art-dark: #111111;
  }
  * { margin: 0; padding: 0; box-sizing: border-box; }
  html, body { width: 1200px; height: 960px; overflow: hidden; }
  body { background: var(--backdrop); position: relative; }

  .card { position: absolute; width: 600px; height: 343px; overflow: hidden; }
  .card-front { left: 322px; top: 110px; background: var(--ink); }
  .card-back { left: 320px; top: 493px; background: var(--back-paper); }

  .front-shape { position: absolute; inset: 0; }

  .identity { position: absolute; left: 30px; top: 82px; color: var(--paper); }
  .identity__name { font: 700 19px/1.1 "Arvo", serif; letter-spacing: .3px; }
  .identity__role { font: 700 14px/1.3 "Arvo", serif; letter-spacing: .3px; }

  .address { position: absolute; left: 30px; top: 134px; color: var(--paper); font: 13px/18px "PT Serif", serif; }

  .contacts { position: absolute; left: 30px; top: 180px; list-style: none; color: var(--paper); font: 12.5px/19.5px "PT Serif", serif; }
  .contacts li { display: flex; align-items: center; gap: 8px; }
  .contacts svg { width: 13px; height: 13px; fill: var(--paper); flex: none; }

  .brand { position: absolute; left: 330px; top: 112px; width: 220px; text-align: center; color: var(--ink); display: flex; flex-direction: column; align-items: center; gap: 12px; }
  .brand__dot { width: 40px; height: 40px; border-radius: 50%; background: var(--ink); }
  .brand__name { font: 700 24px/1.15 "Arvo", serif; }

  .services { position: absolute; top: 49px; left: 0; width: 100%; text-align: center; font: 400 19px/1 "Fjalla One", sans-serif; color: var(--ink); transform: scaleX(.86); }

  .vehicle-art {
    position: absolute; left: 20px; top: 112px; width: 552px; height: 196px;
    background: radial-gradient(ellipse at 45% 40%, var(--art-light) 0%, var(--art-mid) 55%, var(--art-dark) 100%);
    border-radius: 45% 40% 30% 30% / 60% 55% 40% 40%;
  }
  .ground-band { position: absolute; left: 0; bottom: 0; width: 600px; height: 62px; }
  .slogan { position: absolute; left: 0; width: 100%; bottom: 19px; text-align: center; font: 700 16px/1 "Roboto", sans-serif; color: var(--paper); letter-spacing: .3px; }
</style>
</head>
<body>

<section class="card card-front">
  <svg class="front-shape" viewBox="0 0 600 343" aria-hidden="true">
    <circle cx="413" cy="172" r="185" fill="none" stroke="var(--paper)" stroke-width="3"/>
    <circle cx="413" cy="172" r="178" fill="var(--paper)"/>
    <rect x="413" y="0" width="187" height="343" fill="var(--paper)"/>
  </svg>

  <div class="identity">
    <p class="identity__name">MARK DALTON</p>
    <p class="identity__role">CEO/FOUNDER</p>
  </div>

  <p class="address">3847 E Larkin Ave<br>Spokane WA 99214</p>

  <ul class="contacts">
    <li><svg viewBox="0 0 16 16"><path d="M3 1l3 0 1 4-2 1c1 2 3 4 5 5l1-2 4 1 0 3c0 1-1 2-2 2C7 15 1 9 1 3c0-1 1-2 2-2z"/></svg>208.417.6352</li>
    <li><svg viewBox="0 0 16 16"><path d="M4 0h8a1 1 0 011 1v14a1 1 0 01-1 1H4a1 1 0 01-1-1V1a1 1 0 011-1zm1 2v10h6V2zm3 11a1 1 0 100 2 1 1 0 000-2z"/></svg>836 271 5048</li>
    <li><svg viewBox="0 0 16 16"><path d="M1 3h14v1L8 9 1 4zm0 3l7 5 7-5v7H1z"/></svg>BrisksPolish@mailvexo.com</li>
    <li><svg viewBox="0 0 16 16"><path d="M8 1a7 7 0 100 14A7 7 0 008 1zm-1 2c1 1 0 2 1 3s2 0 2 2-2 1-2 3 1 2 0 3c-3-1-5-3-5-6 0-2 2-4 4-5zm4 1c1 1 2 2 2 4h-2c0-1 1-2 0-4z"/></svg>www.briskspolish.com</li>
  </ul>

  <div class="brand">
    <span class="brand__dot"></span>
    <p class="brand__name">Brisk's<br>Polish Works</p>
  </div>
</section>

<section class="card card-back">
  <p class="services">we offer services on anything including cars, trucks, motorcycles &amp; RVs</p>
  <div class="vehicle-art" role="img" aria-label="Black and white illustration of a hot rod car in side view"></div>
  <svg class="ground-band" viewBox="0 0 600 62" preserveAspectRatio="none" aria-hidden="true">
    <path d="M0 62 L0 34 Q300 -14 600 34 L600 62 Z" fill="var(--ink)"/>
  </svg>
  <p class="slogan">WE TAKE PRIDE IN YOUR RIDE</p>
</section>

</body>
</html>
```